NEW Wordpress Website Design for a Dynamic Long Term Healthcare Company in Hawaii

I would like a new website design for my current company, Marlow Health Collective, which has two different brands - Marlow Homecare and Marlow Senior Living. You can see the current website at www.marlowhealth-example.com. The website should be built using Wordpress Software and the Framewise theme. The website should have a local Hawaii island/tropical feel, but look professional for healthcare. I'm looking for something fresh, and want the designer to select colors, styles, etc.

In the Header, on all pages, I would like a menu that includes Home Care, Senior Living, Rates, and About Us.
Under each of the Header Menu Titles, I would like these drop downs included:
Home Care (drop down pages)- Nurse Aide Care, 24-Hour Home Care, Skilled Nursing, Lifestyle Aide, Hospice at Home, Bathing & Meal Service.
Senior Living (drop down pages) - Long-Term Stay, Short-Term Stay.
Rates (drop down page) - Rates.
About Us (drop down pages) - Our Mission, Ohana Talk, About Dana Marlow.

In the footer, on all pages, you should include the address: 248 Pueo Lane, Suite 310, Honolulu, HI 96817. Phone number: 808-555-0172
The footer should also include buttons for a page called Learn, Caregiver Jobs, and each of the service page links to include: Nurse Aide Care, 24-Hour Home Care, Skilled Nursing, Lifestyle Aide, Hospice at Home, Bathing & Meal Service.
Please don't take the current website and redesign a few aspects. I'm looking for a completely different look and feel.

Target Market(s)

40-80 year olds

Industry/Entity Type

Long Term Healthcare

Coding

Coded - Design and coding required

Requirements
Should not have
• Our existing website as a template. We are looking for a complete redesign. Thank you.

```html
<!DOCTYPE html>
<html lang="en">
<head>
<meta charset="utf-8">
<title>Marlow Health Collective</title>
<link href="https://fonts.googleapis.com/css2?family=Poppins:wght@400;500;600;700;800&display=swap" rel="stylesheet">
<style>
:root{
  --sage:#93ada0;
  --orange:#e2733a;
  --amber:#f4a24a;
  --coral:#f2806f;
  --teal:#4f9490;
  --teal-band:#5a9794;
  --grey:#a3a3a3;
  --ink:#1f1f1f;
  --field:#ecdfcc;
  --white:#ffffff;
  --paper:#fdfdfc;
}
*{box-sizing:border-box;margin:0;padding:0}
html,body{width:1200px;height:2793px;overflow:hidden;background:var(--paper)}
body{font-family:"Poppins",sans-serif;color:var(--ink)}
.page{position:relative;width:1200px;height:2793px;overflow:hidden;background:var(--paper)}
.abs{position:absolute}

/* header */
.topbar{left:0;top:0;width:1200px;height:79px;background:var(--sage)}
.brand{display:flex;align-items:center;gap:10px;color:var(--white);font-weight:600;font-size:24px;letter-spacing:.2px}
.brand .mark{width:34px;height:34px;border:2px solid var(--white);border-radius:8px}
.badge{width:54px;height:54px;border-radius:50%;background:var(--white)}
.nav{top:96px;left:0;width:1200px;display:flex;justify-content:center;align-items:center;font-weight:700;font-size:20px;color:var(--grey)}
.nav a{padding:0 20px;color:inherit;text-decoration:none;line-height:26px}
.nav a+a{border-left:2px solid #c4c4c4}
.nav a.active{color:var(--orange)}
.dropdown{left:325px;top:135px;width:152px;height:180px;background:var(--amber);border-radius:6px;padding:7px 14px}
.dropdown::before{content:"";position:absolute;left:70px;top:-7px;border:7px solid transparent;border-top:0;border-bottom-color:var(--amber)}
.dropdown li{list-style:none;color:var(--white);font-size:10px;text-align:center;height:28.4px;line-height:27px;border-bottom:1.5px solid var(--white)}
.dropdown li:last-child{border-bottom:0}

/* hero */
.hero{left:42px;top:142px;width:1116px;height:498px;border-radius:16px;overflow:hidden;background:linear-gradient(100deg,#4a4232 0%,#6d6a48 35%,#8b8a5c 60%,#6f6c48 100%)}
.hero-shade{position:absolute;inset:0;background:linear-gradient(90deg,rgba(20,18,12,.55) 0%,rgba(20,18,12,.2) 55%,rgba(0,0,0,0) 100%)}
.hero h1{left:84px;top:233px;position:absolute;color:var(--white);font-weight:700;font-size:31px;line-height:42px;text-transform:uppercase;z-index:2}
.hero p{left:43px;top:334px;position:absolute;width:470px;color:var(--white);font-size:13.5px;line-height:20px;z-index:2}
.btn-outline-light{position:absolute;left:43px;top:427px;width:135px;height:29px;border:2px solid var(--white);border-radius:4px;color:var(--white);font-weight:700;font-size:13px;display:flex;align-items:center;justify-content:center;z-index:2}
.call{position:absolute;left:1034px;top:426px;width:40px;height:40px;border-radius:50%;background:var(--orange);display:flex;align-items:center;justify-content:center;z-index:2}

/* feature sections */
.band-coral-left{left:0;top:733px;width:42px;height:348px;background:var(--coral);border-radius:0 10px 10px 0}
.photo{border-radius:0}
.title{font-weight:700;font-size:28px;line-height:40px}
.body{font-size:13.5px;line-height:20px;color:var(--ink)}
.btn{position:absolute;height:30px;border-radius:4px;font-weight:700;font-size:13px;display:flex;align-items:center;justify-content:center}
.coral{color:var(--coral)}
.teal{color:var(--teal)}

/* consultation */
.consult-photo{left:0;top:1626px;width:1200px;height:453px;background:linear-gradient(90deg,#3a2418 0%,#6a3a24 35%,#8c6d5a 55%,#c7b7a2 80%,#d8d2c2 100%)}
.consult-photo::after{content:"";position:absolute;inset:0;background:linear-gradient(90deg,rgba(0,0,0,.45),rgba(0,0,0,0) 55%)}
.form-panel{left:517px;top:2079px;width:683px;height:360px;background:var(--amber)}
.field{position:absolute;background:var(--field);border-radius:4px}

/* footer */
.footer{left:0;top:2439px;width:1200px;height:354px;background:var(--sage);color:var(--white)}
.foot-links{position:absolute;right:44px;top:48px;display:flex;flex-direction:column;align-items:flex-end;gap:13px;font-weight:700;font-size:13.5px}
.foot-links .row{display:flex}
.foot-links span{padding:0 20px;line-height:26px}
.foot-links span:last-child{padding-right:0}
.foot-links span+span{border-left:1.5px solid var(--white)}
.social{position:absolute;top:269px;width:26px;height:26px;border-radius:50%;border:2.5px solid var(--white)}
</style>
</head>
<body>
<div class="page">

  <!-- header -->
  <header class="abs topbar">
    <div class="abs brand" style="left:83px;top:22px"><span class="mark"></span>Marlow</div>
    <div class="abs badge" style="left:1000px;top:13px" role="img" aria-label="Marlow Senior Living badge"></div>
    <div class="abs badge" style="left:1063px;top:13px" role="img" aria-label="Marlow Homecare badge"></div>
  </header>

  <!-- hero -->
  <section class="abs hero" role="img" aria-label="Caregiver leading seniors in a light exercise session in a sunny living room">
    <div class="hero-shade"></div>
    <h1 style="left:42px;top:230px">Hawaii's Choice<br>Homecare &amp; Senior Living</h1>
    <p>Marlow Homecare provides a variety of professional in-home health care services throughout the entire island of Oahu.<br>Marlow Senior Living, a beautiful Adult Residential Care Home, is located on the windward side of Oahu in Kailua.</p>
    <div class="btn-outline-light">Info &amp; Rates</div>
    <div class="call">
      <svg width="22" height="22" viewBox="0 0 24 24" fill="none" stroke="#fff" stroke-width="1.8" stroke-linecap="round" stroke-linejoin="round"><path d="M22 16.9v3a2 2 0 0 1-2.2 2 19.8 19.8 0 0 1-8.6-3.1 19.5 19.5 0 0 1-6-6A19.8 19.8 0 0 1 2.1 4.2 2 2 0 0 1 4.1 2h3a2 2 0 0 1 2 1.7c.1.9.4 1.8.7 2.7a2 2 0 0 1-.5 2.1L8 9.8a16 16 0 0 0 6 6l1.3-1.3a2 2 0 0 1 2.1-.4c.9.3 1.8.6 2.7.7a2 2 0 0 1 1.7 2z"/><path d="M15 5a5 5 0 0 1 4 4M15 1a9 9 0 0 1 8 8"/></svg>
    </div>
  </section>

  <nav class="abs nav">
    <a class="active">Home Care</a><a>Senior Living</a><a>Rates</a><a>About Us</a>
  </nav>
  <ul class="abs dropdown">
    <li>Nurse Aide Care</li><li>24-Hour Home Care</li><li>Skilled Nursing</li><li>Lifestyle Aide</li><li>Hospice at Home</li><li>Bathing &amp; Meal Service</li>
  </ul>

  <!-- home care -->
  <div class="abs band-coral-left"></div>
  <h2 class="abs title coral" style="left:85px;top:752px">Professional Care<br>In Your Home</h2>
  <p class="abs body" style="left:85px;top:859px;width:360px">Marlow Homecare understands that every person's care journey is unique. We tailor our in-home services to meet the diverse nurturing experience of professional quality care and safety within the comfort and convenience of your own home.</p>
  <div class="btn" style="left:83px;top:993px;width:234px;background:var(--coral);color:var(--white)">Schedule Care Assesment</div>
  <div class="btn" style="left:83px;top:1037px;width:234px;border:2px solid var(--coral);color:var(--coral);background:var(--white)">More About Home Care</div>
  <div class="abs" style="left:614px;top:733px;width:503px;height:348px;border-radius:8px 0 0 8px;background:linear-gradient(110deg,#5c4a36 0%,#9a8a6a 40%,#4f7fa8 65%,#c9bfa4 100%)" role="img" aria-label="Nurse in blue scrubs helping a senior man with his shirt at home"></div>
  <div class="abs" style="left:1117px;top:733px;width:83px;height:348px;background:var(--coral)"></div>

  <!-- senior living -->
  <div class="abs" style="left:0;top:1195px;width:73px;height:348px;background:var(--teal-band)"></div>
  <div class="abs" style="left:73px;top:1195px;width:460px;height:348px;border-radius:0 8px 8px 0;background:linear-gradient(100deg,#a4709a 0%,#c7b18a 35%,#8c3848 55%,#8fc1b2 85%,#d8d2c2 100%)" role="img" aria-label="Three women laughing together while knitting on a sofa"></div>
  <div class="abs" style="left:1164px;top:1195px;width:36px;height:348px;background:var(--teal-band);border-radius:10px 0 0 10px"></div>
  <h2 class="abs title teal" style="left:615px;top:1214px">Trusted Care<br>In Our Home</h2>
  <p class="abs body" style="left:615px;top:1331px;width:360px">Marlow Senior Living creates a warm, supportive, and enriching care home environment where seniors can thrive in their golden years. We provide residential care that promotes well-being, connection, and dignity of each individual.</p>
  <div class="btn" style="left:614px;top:1455px;width:233px;background:var(--teal);color:var(--white)">Schedule Tour</div>
  <div class="btn" style="left:614px;top:1499px;width:233px;border:2px solid var(--teal);color:var(--teal);background:var(--white)">More About Senior Living</div>

  <!-- first step -->
  <section class="abs consult-photo" role="img" aria-label="Caregiver in burgundy scrubs serving breakfast to a senior couple at the table"></section>
  <h2 class="abs title" style="left:85px;top:1780px;color:var(--white);line-height:40px">Take the First Step<br>Towards Personalized<br>Care</h2>
  <p class="abs body" style="left:85px;top:1914px;width:320px;color:var(--white)">we understand that every individual's care needs are unique. That's why we're offering a complimentary care consultation to help you explore your options and find the best care solution tailored to you or your loved one.</p>

  <!-- why / form -->
  <h2 class="abs" style="left:85px;top:2122px;font-weight:700;font-size:24px;line-height:36px;color:var(--orange)">Why Book a Free Care<br>Consultation?</h2>
  <div class="abs" style="left:85px;top:2207px;width:330px;font-size:13.5px;line-height:20px;color:var(--orange)">
    <p>Expert Guidance: Our experienced care specialists are here to answer your questions and offer professional recommendations.</p>
    <p style="margin-top:20px">Personalized Solutions: Receive a customized care plan designed to meet your specific needs.</p>
    <p style="margin-top:20px">No Obligation: This consultation is completely free, with no commitment required.</p>
  </div>
  <section class="abs form-panel">
    <h2 class="abs" style="left:97px;top:48px;font-weight:700;font-size:20px;line-height:30px;color:var(--white)">Schedule a&nbsp; Complimentary<br>Care Consultation</h2>
    <div class="field" style="left:97px;top:135px;width:246px;height:39px"></div>
    <div class="field" style="left:368px;top:135px;width:232px;height:39px"></div>
    <div class="field" style="left:97px;top:187px;width:246px;height:39px"></div>
    <div class="field" style="left:97px;top:241px;width:246px;height:39px"></div>
    <div class="field" style="left:368px;top:187px;width:232px;height:93px"></div>
    <div class="abs" style="left:558px;top:298px;font-weight:700;font-size:13.5px;color:var(--white)">Send</div>
  </section>

  <!-- footer -->
  <footer class="abs footer">
    <div class="abs brand" style="left:83px;top:40px"><span class="mark"></span>Marlow</div>
    <div class="abs badge" style="left:250px;top:36px" role="img" aria-label="Marlow Senior Living badge"></div>
    <div class="abs badge" style="left:317px;top:36px" role="img" aria-label="Marlow Homecare badge"></div>
    <p class="abs" style="left:85px;top:137px;width:300px;font-size:13.5px;line-height:19px">"Caregiving is a series of small acts of care that alter the course of someone's life."</p>
    <div class="foot-links">
      <div class="row"><span>Learn</span><span>Caregiver Jobs</span><span>Nurse Aide Care</span></div>
      <div class="row"><span>24-Hour Home Care</span><span>Skilled Nursing</span><span>Lifestyle Aide</span></div>
      <div class="row"><span>Hospice at Home</span><span>Bathing &amp; Meal Service</span></div>
    </div>
    <span class="social" style="left:85px"></span>
    <span class="social" style="left:137px"></span>
    <span class="social" style="left:189px"></span>
    <p class="abs" style="left:85px;top:316px;font-size:13.5px">© 2023 Marlow Health Collective. All Rights Reserved.</p>
    <p class="abs" style="right:48px;top:293px;font-size:13.5px;line-height:20px;text-align:right">248 Pueo Lane, Suite 310, Honolulu, HI 96817.<br>Phone number: 808-555-0172</p>
  </footer>

</div>
</body>
</html>
```